Tovimar Community Development Planning New web site

Design a new web site. I have a budget of $1,500.00.
Attached on PowerPoint is a complete site plan. Home page and linked pages.
10 - 12 pages. All copy and photos will be supplied. (300dpi)
I have shown them the concept which they like.
No data bases required. Home page with animations dissolving.
They former web site has been taken down. They have been in business 30 years in New Jersey
Colors teal blues and greens
There will be a new logo)being designed)
The text in home page copy will give you a detailed story what they are all about.

files have been approved for Tovimar, Inc.   Brenton is the designer

```html
<!DOCTYPE html>
<html lang="en">
<head>
<meta charset="utf-8">
<title>Tovimar, Inc. — Community Development Planning</title>
<link href="https://fonts.googleapis.com/css2?family=Lato:wght@400;700&family=Open+Sans:wght@400;600&display=swap" rel="stylesheet">
<style>
:root{
  --green:#4a9e16;
  --gold:#f5c10e;
  --blue:#5c9bd1;
  --ink:#1f1f1f;
  --muted:#777;
  --rule:#e5ecf3;
  --band:rgba(110,110,110,.88);
}
*{margin:0;padding:0;box-sizing:border-box}
html,body{width:1051px;height:1200px;overflow:hidden;background:#fff}
body{position:relative;font-family:"Open Sans",sans-serif;color:var(--ink)}
.topbar{position:absolute;left:0;top:0;width:1051px;height:45px;background:var(--green)}
.brand{position:absolute;left:111px;top:11px;display:flex;align-items:center;gap:6px;color:#fff;font-family:"Lato",sans-serif;font-weight:700;font-size:19px}
.brand .mark{width:10px;height:10px;background:#fff}
.nav{position:absolute;right:110px;top:0;height:45px;display:flex;font-family:"Lato",sans-serif;font-size:12.5px;text-transform:uppercase}
.nav a{color:#fff;text-decoration:none;padding:0 6px;line-height:45px;border-left:1px solid rgba(0,0,0,.12)}
.nav a:first-child{border-left:none}
.nav a.active{color:var(--gold)}
.hero{position:absolute;left:0;top:45px;width:1051px;height:467px;background:linear-gradient(160deg,#fafafa 0%,#eeeeee 50%,#f4f1ee 100%)}
.hero-band{position:absolute;left:0;top:364px;width:1051px;height:148px;background:var(--band)}
.services{position:absolute;left:111px;top:395px;list-style:none;color:#fff;font-family:"Lato",sans-serif;font-size:13px}
.services li{height:22.4px;display:flex;align-items:center;gap:5px}
.services li svg{flex:none}
.cta{position:absolute;left:769px;top:437px;width:172px;height:40px;background:var(--gold);color:#333;font-family:"Lato",sans-serif;font-size:14px;display:flex;align-items:center;justify-content:center;gap:8px;text-transform:uppercase;border:1px solid #e0ac00}
.col{position:absolute;top:585px}
.col h2{font-family:"Lato",sans-serif;font-weight:400;font-size:20px;color:var(--blue);letter-spacing:.3px;padding-bottom:10px;border-bottom:3px solid var(--rule)}
.col-left{left:111px;width:390px}
.col-left p{font-size:11px;line-height:15.8px;margin-top:16px}
.col-left h2+p{margin-top:21px}
.divider{position:absolute;left:526px;top:565px;width:1px;height:400px;background:#e3e3e3}
.col-right{left:556px;width:385px}
.results{list-style:none;margin-top:13px}
.results li{display:flex;gap:6px;font-size:11px;line-height:15.8px;padding:6px 2px 8px;border-bottom:1px solid #d6d6d6}
.results li:last-child{border-bottom:none}
.results li svg{flex:none;margin-top:3px}
.results li.highlight{color:#d7a600}
.contact-note{font-size:15px;line-height:19px;margin-top:7px;color:#111}
.contact-note span{color:var(--blue)}
.members{position:absolute;left:0;top:1017px;width:1051px;height:122px;background:var(--green);color:#fff;text-align:center}
.members h3{font-family:"Lato",sans-serif;font-weight:400;font-size:20px;margin-top:27px}
.members p{font-size:11px;line-height:16px;margin-top:4px}
.footer{position:absolute;left:111px;top:1158px;width:830px;display:flex;justify-content:space-between;font-size:9px;color:#666}
.footer .terms{color:#222;font-size:8px}
</style>
</head>
<body>
<header class="topbar">
  <div class="brand"><span class="mark"></span>Tovimar Inc.</div>
  <nav class="nav">
    <a href="#">Home</a><a href="#">Company</a><a href="#">Services</a><a href="#" class="active">Housing Rehab Application</a><a href="#">Affordable Application</a><a href="#">Contact</a>
  </nav>
</header>

<div class="hero" role="img" aria-label="Word collage around the word community: performance, concept, innovation, vision, management, achievement, strategy, mentor, training"></div>
<div class="hero-band">
</div>
<ul class="services">
  <li><svg width="10" height="10"><circle cx="5" cy="5" r="5" fill="#f5c10e"/><circle cx="5" cy="5" r="1.6" fill="#555"/></svg>Community Development Planning</li>
  <li><svg width="10" height="10"><circle cx="5" cy="5" r="5" fill="#f5c10e"/><circle cx="5" cy="5" r="1.6" fill="#555"/></svg>Housing Rehabilitation Administration</li>
  <li><svg width="10" height="10"><circle cx="5" cy="5" r="5" fill="#f5c10e"/><circle cx="5" cy="5" r="1.6" fill="#555"/></svg>US Department of Housing and Urban Development (HUD) Program Management</li>
  <li><svg width="10" height="10"><circle cx="5" cy="5" r="5" fill="#f5c10e"/><circle cx="5" cy="5" r="1.6" fill="#555"/></svg>Implementation of Programs under the Jurisdiction of New Jersey Council of Affordable Housing (COAH)</li>
</ul>
<a class="cta" href="#">Call to Action <svg width="8" height="10"><path d="M2 1l4 4-4 4" stroke="#333" stroke-width="2" fill="none"/></svg></a>

<section class="col col-left">
  <h2>WELCOME TO TOVIMAR</h2>
  <p>Tovimar, Inc. is a city planning firm that specializes in community development and housing rehabilitation program planning, design and implementation. We have over twenty years of experience in developing and administering income base-base housing and programs in accordance with US Department of Housing and Urban Development (HUD) and New Jersey Council on Affordable Housing (COAH) rules and regulations,</p>
  <p>In addition, our firm is capable of providing the technical and administrative assistance our clients require for implementation of their income based housing programs. H. Calder Wynne Associates is one of the most experience urban planning firms in New Jersey, with over forty years of as consulting planners.</p>
  <p>To find out more about federal housing programs that we will administer, please go to www.housingprograms.example</p>
</section>

<div class="divider"></div>

<section class="col col-right">
  <h2>WE GET RESULTS</h2>
  <ul class="results">
    <li><svg width="12" height="10"><path d="M1 5l3.5 3.5L11 1" stroke="#aaa" stroke-width="2" fill="none"/></svg>Tovimar designs income based programs to be supported by federal placement lotteries state funding.</li>
    <li><svg width="12" height="10"><path d="M1 5l3.5 3.5L11 1" stroke="#aaa" stroke-width="2" fill="none"/></svg>We implement local programs to benefit people seeking access to affordable housing.</li>
    <li><svg width="12" height="10"><path d="M1 5l3.5 3.5L11 1" stroke="#aaa" stroke-width="2" fill="none"/></svg>Our experienced staff screen applicants for local affordable housing.</li>
    <li><svg width="12" height="10"><path d="M1 5l3.5 3.5L11 1" stroke="#aaa" stroke-width="2" fill="none"/></svg>We pre-qualify persons who have applied for housing rehabilitation.</li>
    <li class="highlight"><svg width="12" height="10"><path d="M1 5l3.5 3.5L11 1" stroke="#f5c10e" stroke-width="2.4" fill="none"/></svg>Conduct placement lotteries</li>
    <li><svg width="12" height="10"><path d="M1 5l3.5 3.5L11 1" stroke="#aaa" stroke-width="2" fill="none"/></svg>Through local housing rehabilitation programs, our experience construction inspectors determine what improvements are required at eligible units based on local building codes and health and safety issues.</li>
  </ul>
  <p class="contact-note">For more information about out services,<br>please contact us today at <span>TOVIMAR (555) 014-2290 or tovimar@mailbox.example</span></p>
</section>

<section class="members">
  <h3>MEMBERSHIPS</h3>
  <p>National Neighborhood Renewal Council &nbsp;&nbsp; Garden State Planning Society<br>Coastal Planning Officials Forum &nbsp;Shoreline Community Housing Alliance</p>
</section>

<footer class="footer">
  <span>Copy Right 2014 Tovimar, 218 Larkspur Road, Seabrook, New Jersey, 08900 &nbsp;&nbsp; TEL (555) 014-2290 Fax (555) 014-2291</span>
  <span class="terms">©2014 - Terms</span>
</footer>
</body>
</html>
```